Business Cards for new orthopaedic surgery practice

My husband and I are starting our own orthopaedic surgery practice. We are looking for a business card that is uniform, but one will have my name/title and the other will have his. You can just create one design with my name on it for now. But when I choose your design as the winning design I will ask that you add another copy with his name/title.

We are looking for classy, simple, elite all in one. We like dark blues/a little gold/yellow. Something that goes with our logo. We want our logo incorporated. Here is all the info you need:
Business name: RV Bone & Vitality Center
Location: 38517 North Willowmere Ave
Coral Springs, FL 33071
Phone: 954-218-4063
Fax: 954-582-7341
Email: info@myrvbonecare.example

Names: Lydia Vance, M.D.
Board Certified Hand and Upper Extremity Surgeon

Ebo Dansu, M.D.
Board Certified Hip & Knee Replacement/General Orthopaedic Surgeon

Can decide what you want to put on the back. Maybe a slogan:
Rooted in Care. Focused on You

I am just going to upload our logo. The only thing is if we select you as the winning design, the location, and phone numbers may change. We will need your help to update that once fully solidified.

Industry/Entity Type

Medical

Contact Information for Business Card

Colors
0054AA
0677BA
7BADD7
CADEEF
E8F1F8
0094D4
00A9DD
6FCCEA
C7EBF8
E9F6FB

Requirements
Must have
• class, appeal,
Should not have
• We want to air on the side of masculine if we are looking at masculine vs. feminine feel. But we still want it classy, sophisticated, and something we will love

```html
<!DOCTYPE html>
<html lang="en">
<head>
<meta charset="utf-8">
<title>RV Bone &amp; Vitality Center – Business Card</title>
<link href="https://fonts.googleapis.com/css2?family=Tinos:wght@400;700&display=swap" rel="stylesheet">
<style>
  :root {
    --cyan: #1dbce3;
    --navy: #273f82;
    --white: #ffffff;
    --backdrop: #f1f1f1;
  }
  * { margin: 0; padding: 0; box-sizing: border-box; }
  html, body {
    width: 1200px; height: 990px; overflow: hidden;
    background: var(--backdrop);
    font-family: "Tinos", "Times New Roman", serif;
  }
  .card {
    position: absolute;
    left: 244px;
    width: 712px; height: 407px;
    border-radius: 46px;
    overflow: hidden;
    box-shadow: 0 10px 22px rgba(0,0,0,.28);
  }

  /* Front */
  .card-front { top: 68px; background: var(--cyan); color: var(--white); }
  .front-mark {
    position: absolute; left: 50%; top: 118px;
    width: 84px; height: 84px; margin-left: -42px;
    border-radius: 50%; background: var(--white);
  }
  .front-name {
    position: absolute; left: 0; right: 0; top: 222px;
    text-align: center;
    font-size: 34px; font-weight: 400; letter-spacing: 1px;
    text-transform: uppercase; line-height: 36px;
  }
  .tagline {
    position: absolute; left: 0; right: 0; top: 357px;
    text-align: center; font-size: 18px; letter-spacing: .4px;
  }
  .tagline .bullet {
    display: inline-block; width: 7px; height: 7px; border-radius: 50%;
    background: var(--white); margin: 0 6px 2px 10px; vertical-align: middle;
  }

  /* Back */
  .card-back { top: 516px; background: var(--white); }
  .side-band { position: absolute; left: 0; top: 0; width: 84px; height: 100%; background: var(--cyan); }
  .side-tab { position: absolute; right: 0; top: 144px; width: 18px; height: 59px; background: var(--cyan); }

  .feature-mark {
    position: absolute; left: 40px; top: 18px;
    width: 120px; height: 120px; border-radius: 50%;
    background: var(--navy);
  }
  .feature-name {
    position: absolute; left: 28px; top: 168px;
    color: var(--navy); font-size: 62px; line-height: 72px;
    text-transform: uppercase; letter-spacing: 1px; white-space: nowrap;
  }

  .header-mark {
    position: absolute; left: 445px; top: 48px;
    width: 70px; height: 70px; border-radius: 50%; background: var(--navy);
  }
  .header-divider {
    position: absolute; left: 560px; top: 52px;
    width: 2px; height: 74px; background: var(--navy);
  }
  .back-name {
    position: absolute; left: 574px; top: 56px;
    color: var(--navy); font-size: 19px; line-height: 21px;
    text-transform: uppercase; letter-spacing: .3px;
  }

  .details { position: absolute; right: 30px; top: 0; width: 440px; height: 100%; text-align: right; }
  .doctor-name {
    position: absolute; right: 0; top: 138px; white-space: nowrap;
    color: var(--cyan); font-weight: 700; font-size: 26px; letter-spacing: 1px;
  }
  .doctor-title {
    position: absolute; right: 0; top: 164px; white-space: nowrap;
    color: var(--navy); font-size: 17px; line-height: 23px; letter-spacing: .3px;
  }
  .address {
    position: absolute; right: 0; top: 229px; white-space: nowrap;
    color: var(--cyan); font-size: 17px; line-height: 23px; letter-spacing: .4px;
  }
  .contact-list {
    position: absolute; right: 0; top: 291px; list-style: none;
    color: var(--navy); font-size: 17px; line-height: 23px; letter-spacing: .3px;
  }
  .contact-list li { display: flex; justify-content: flex-end; align-items: center; white-space: nowrap; }
  .contact-list svg { width: 15px; height: 15px; margin-left: 8px; flex: none; }
</style>
</head>
<body>

<section class="card card-front">
  <div class="front-mark"></div>
  <p class="front-name">RV Bone &amp; Vitality<br>Center</p>
  <p class="tagline"><span class="bullet"></span>Rooted in Care <span class="bullet"></span>Focused on You</p>
</section>

<section class="card card-back">
  <div class="side-band"></div>
  <div class="side-tab"></div>

  <div class="feature-mark"></div>
  <p class="feature-name">RV Bone &amp;<br>Vitality<br>Center</p>

  <div class="header-mark"></div>
  <div class="header-divider"></div>
  <p class="back-name">RV Bone &amp;<br>Vitality<br>Center</p>

  <div class="details">
    <h1 class="doctor-name">Lydia Vance, M.D.</h1>
    <p class="doctor-title">Board Certified Hand and<br>Upper Extremity Surgeon</p>
    <p class="address">38517 North Willowmere Ave<br>Coral Springs, FL 33071</p>
    <ul class="contact-list">
      <li>954-218-4063
        <svg viewBox="0 0 16 16" fill="none" stroke="#1dbce3" stroke-width="1.6"><path d="M4 2l2 3-1.5 1.5c.8 2 2.5 3.7 4.5 4.5L10.5 9.5l3 2-1.2 2.3C7.5 13.5 2.5 8.5 2 3.5z"/></svg>
      </li>
      <li>954-582-7341
        <svg viewBox="0 0 16 16" fill="#1dbce3"><rect x="2" y="6" width="12" height="8" rx="1"/><rect x="5" y="2" width="7" height="5" fill="none" stroke="#1dbce3" stroke-width="1.4"/></svg>
      </li>
      <li>www.myrvbonecare.example
        <svg viewBox="0 0 16 16" fill="none" stroke="#1dbce3" stroke-width="1.3"><circle cx="8" cy="8" r="6.5"/><ellipse cx="8" cy="8" rx="3" ry="6.5"/><path d="M1.5 8h13M2.5 4.8h11M2.5 11.2h11"/></svg>
      </li>
      <li>info@myrvbonecare.example
        <svg viewBox="0 0 16 16" fill="none" stroke="#1dbce3" stroke-width="1.4"><rect x="1.5" y="4" width="13" height="10" rx="1"/><path d="M1.5 5l6.5 5 6.5-5"/></svg>
      </li>
    </ul>
  </div>
</section>

</body>
</html>
```